Professional violinist needs business cards

I am trying to attract the following jobs:
-private violin lessons (primarily classical)
-performance gigs (weddings, birthday parties, funerals, etc.)
-collaborations with other artists (studio recordings, performances)

I want to communicate that I have a very high standard of excellence for my work, but I also love people and celebrations.
Values/style words I like are:
love, joy, peace, fun, beauty, authenticity, excellence, warmth, refined/sleek, free spirited. If that's too confusing, just ignore :)

I will attach my favorite business card template that I could find on Canva. The lines are supposed to be like a music staff, which I think is really cool, but I also don't want it to look too busy. I like the simple black and white--I think it looks sharp--but I also am open to other ideas. I also have seen business cards with pictures included that looked great, so I attached an image that could be used as well.

I am also attaching a file that I made of my initials that could be used as a logo, but I'm not sure if it should be included.

Information on the card:
-My name (18 letters total)
-"violinist"
-phone number, email, website

Thank you!

```html
<!DOCTYPE html>
<html lang="en">
<head>
<meta charset="utf-8">
<title>Marianne Holloway – Violinist Business Cards</title>
<link href="https://fonts.googleapis.com/css2?family=Dancing+Script:wght@500&family=Cinzel:wght@500&family=Lora&display=swap" rel="stylesheet">
<style>
  :root{
    --page:#2b2b2c;
    --card-top:#252a2f;
    --card-bottom:#1e2226;
    --gold:#c8b48d;
    --ink:#ecebe8;
    --silver-a:#e9e9ea;
    --silver-b:#c9cacc;
  }
  *{margin:0;padding:0;box-sizing:border-box}
  html,body{width:1200px;height:1138px;overflow:hidden;background:var(--page)}
  .canvas{position:relative;width:1200px;height:1138px}
  .card{
    position:absolute;width:620px;height:374px;border-radius:14px;overflow:hidden;
    background:linear-gradient(170deg,var(--card-top),var(--card-bottom));
  }
  .card--front{left:274px;top:186px}
  .card--back{left:276px;top:608px}

  .clef-art{
    position:absolute;left:0;top:0;width:140px;height:374px;
    background:linear-gradient(180deg,var(--silver-a),var(--silver-b));
    opacity:.9;
    border-radius:0 70px 70px 0;
  }

  .mark{
    position:absolute;font-family:"Lora",serif;color:var(--gold);
    line-height:1;letter-spacing:2px;transform:translate(-50%,-50%);
  }
  .name{
    position:absolute;font-family:"Dancing Script",cursive;font-weight:500;
    color:var(--ink);white-space:nowrap;transform:translateX(-50%);line-height:1;
  }
  .role{
    position:absolute;display:flex;align-items:center;gap:18px;transform:translateX(-50%);
    font-family:"Cinzel",serif;font-weight:500;color:var(--ink);letter-spacing:3px;white-space:nowrap;line-height:1;
  }
  .role::before,.role::after{content:"";display:block;height:1px;background:var(--gold);opacity:.8}

  .card--front .mark{left:376px;top:134px;font-size:52px}
  .card--front .name{left:384px;top:204px;font-size:47px}
  .card--front .role{left:384px;top:255px;font-size:19px}
  .card--front .role::before,.card--front .role::after{width:82px}

  .staff-line{position:absolute;left:0;width:100%;height:2px;background:var(--gold)}
  .staff-line--top{top:22px}
  .staff-line--bottom{top:350px}

  .card--back .mark{left:142px;top:120px;font-size:44px}
  .card--back .name{left:353px;top:82px;font-size:40px}
  .card--back .role{left:353px;top:128px;font-size:16px}
  .card--back .role::before,.card--back .role::after{width:70px}

  .contact{
    position:absolute;left:309px;top:202px;transform:translateX(-50%);
    font-family:"Lora",serif;font-size:15.5px;line-height:23.2px;color:var(--ink);
    text-align:center;list-style:none;white-space:nowrap;
  }
  .contact .accent{color:var(--gold)}
</style>
</head>
<body>
<main class="canvas">
  <section class="card card--front">
    <div class="clef-art" role="img" aria-label="Large silver treble clef decoration"></div>
    <div class="mark">MH</div>
    <h1 class="name">Marianne Holloway</h1>
    <p class="role">Violinist</p>
  </section>

  <section class="card card--back">
    <span class="staff-line staff-line--top"></span>
    <div class="mark">MH</div>
    <h2 class="name">Marianne Holloway</h2>
    <p class="role">Violinist</p>
    <ul class="contact">
      <li>+1 (555) 014-2276</li>
      <li>hello@mariannehollowayviolin.com</li>
      <li>www.<span class="accent">mariannehollowayviolin</span>.com</li>
      <li>Alder Springs, VT</li>
    </ul>
    <span class="staff-line staff-line--bottom"></span>
  </section>
</main>
</body>
</html>
```